Business card design needed

Front of Card:
I would like to have nearly 3/4 of the card from the top in a Pea Green Colour with the word 'Brambleway' written in a(Watermelon Red colour) in the font 'Viner Hand ITC'. Brambleway to be written within the Green colour of the card.

The lower 1/3 of the card I would like to have white with the words:
Home and Garden Styling smaller than the word Brambleway in Black in the font 'Batang', centred underneath the green section.

At the very bottom in one corner in smaller print I would like to have my contact phone number: Pia M:0437619204 and then the email address:
E: brambleaystudio@kelnor.net.au on the other side.

Back of Card:
Back of Card to be White
On one side (Left)
I would like the Heading "Garden" in the same pea green colour as the front and in the Viner Hand ITC font. On the other half of the card I would like 'Home' in the Watermelon Red Colour (same as front colour) and in the font Viner Hand ITC.
Underneath these Headings I would like written in black and in Batang font the following list of services.

Garden Home
Garden Styling Interior Styling
Plant Selection Furniture Selection/Arrangement Garden Maintenance Setting Up Home (after move)
Hedging/Mowing Merchandise and Stylist for
Work w/Local Nurseries Marrow and Finch

Brambleway
Home and Garden Styling
M: 0437619204 E: brambleaystudio@kelnor.net.au

```html
<!DOCTYPE html>
<html lang="en">
<head>
<meta charset="utf-8">
<title>Brambleway – Business Card Concepts</title>
<link rel="stylesheet" href="https://fonts.googleapis.com/css2?family=Caveat+Brush&family=Nanum+Myeongjo:wght@400;700&family=Questrial&family=Montserrat:wght@600&display=swap">
<style>
  :root{
    --forest:#217a38;
    --pea:#2b9a12;
    --melon:#e24c6e;
    --melon-bright:#e84b6f;
    --ink:#2a2a2a;
    --muted:#7a7a7a;
    --paper:#ffffff;
    --edge:#d6d6d6;
    --script:"Caveat Brush", cursive;
    --serif:"Nanum Myeongjo", serif;
    --sans:"Questrial", sans-serif;
    --bold-sans:"Montserrat", sans-serif;
  }
  *{box-sizing:border-box;margin:0;padding:0}
  html,body{width:1200px;height:629px;overflow:hidden;background:var(--paper)}
  .sheet{position:relative;width:1200px;height:629px;border:1px solid #e4e4e4;background:var(--paper)}
  .card{position:absolute;overflow:hidden;border:1px solid var(--edge);box-shadow:0 6px 14px rgba(0,0,0,.12);background:var(--paper)}

  /* landscape front */
  .landscape-front{left:32px;top:29px;width:471px;height:263px}
  .landscape-front .band{position:absolute;left:0;top:0;width:100%;height:170px;background:var(--forest);display:flex;align-items:center;justify-content:center}
  .wordmark{font-family:var(--script);color:var(--melon);font-weight:400;line-height:1}
  .landscape-front .wordmark{font-size:76px}
  .landscape-front .tagline{position:absolute;top:178px;width:100%;text-align:center;font-family:var(--serif);font-size:30px;color:var(--ink)}
  .landscape-front .contact{position:absolute;top:235px;left:0;width:100%;display:flex;justify-content:space-between;padding:0 22px 0 20px;font-family:var(--serif);font-weight:700;font-size:16px;color:var(--ink)}
  .contact span{display:flex;align-items:center;gap:5px}

  /* landscape back */
  .landscape-back{left:30px;top:310px;width:471px;height:261px}
  .service-col{position:absolute;top:0}
  .service-col h2{font-family:var(--script);font-weight:400;font-size:38px;line-height:1;position:absolute;white-space:nowrap}
  .service-col ul{list-style:none;position:absolute;font-family:var(--serif);font-size:13.5px;color:var(--ink);line-height:20px;white-space:nowrap}
  .service-col li::before{content:"•";margin-right:5px}
  .landscape-back .garden h2{left:79px;top:30px;color:var(--forest)}
  .landscape-back .garden ul{left:48px;top:98px}
  .landscape-back .garden li::before{color:var(--forest)}
  .landscape-back .home h2{left:315px;top:28px;color:var(--melon)}
  .landscape-back .home ul{left:246px;top:96px}
  .landscape-back .home li::before{color:var(--melon)}
  .landscape-back .stripe{position:absolute;left:0;bottom:0;width:100%;height:16px}

  /* captions */
  .caption{position:absolute;font-family:var(--sans);transform:translateX(-50%);white-space:nowrap}
  .caption.title{left:898px;top:28px;font-size:21px;color:var(--muted)}
  .caption.front{left:746px;top:61px;font-size:21px;color:var(--ink)}
  .caption.back{left:1032px;top:71px;font-size:21px;color:var(--ink)}

  /* portrait front */
  .portrait{width:261px;height:470px;background:var(--pea)}
  .portrait-front{left:615px;top:96px}
  .portrait-back{left:898px;top:98px}
  .portrait .split{position:absolute;left:0;top:0}
  .portrait-front .wordmark{position:absolute;left:128px;top:124px;transform:translate(-50%,-50%) rotate(-22.5deg);font-size:56px;white-space:nowrap}
  .portrait-front .tagline{position:absolute;left:132px;top:206px;transform:translate(-50%,-50%) rotate(-22.5deg);font-family:var(--bold-sans);font-weight:600;font-size:18.5px;color:var(--ink);white-space:nowrap}
  .portrait-front .phone{position:absolute;left:61px;top:306px;font-family:var(--sans);font-size:18px;color:var(--paper);display:flex;align-items:center;gap:4px}
  .portrait-front .email{position:absolute;left:9px;top:380px;font-family:var(--sans);font-size:15.5px;color:var(--paper);letter-spacing:.2px}

  /* portrait back */
  .portrait-back .service-col{left:0;width:100%}
  .portrait-back h2{color:var(--paper);left:0;width:100%;text-align:center;font-size:40px}
  .portrait-back ul{left:22px;font-family:var(--sans);color:var(--paper);font-size:13.5px;line-height:20.5px}
  .portrait-back .garden h2{top:26px}
  .portrait-back .garden ul{top:88px}
  .portrait-back .home h2{top:268px}
  .portrait-back .home ul{top:326px}
</style>
</head>
<body>
<main class="sheet">

  <section class="card landscape-front" aria-label="Card front, landscape">
    <div class="band"><span class="wordmark">Brambleway</span></div>
    <p class="tagline">Home and Garden Styling</p>
    <div class="contact">
      <span><svg width="13" height="16" viewBox="0 0 13 16" aria-hidden="true"><path d="M3 1 L5 4.5 L3.6 6 Q5 9.5 7.5 11.5 L9 10 L12 12.5 L10.5 15 Q3 13 1 4 Z" fill="none" stroke="#2a2a2a" stroke-width="1.3" stroke-linejoin="round"/></svg>0437619204</span>
      <span><svg width="17" height="12" viewBox="0 0 17 12" aria-hidden="true"><rect x="1" y="1" width="15" height="10" fill="none" stroke="#2a2a2a" stroke-width="1.1"/><path d="M1 1 L8.5 7 L16 1" fill="none" stroke="#2a2a2a" stroke-width="1.1"/></svg>brambleaystudio@kelnor.net.au</span>
    </div>
  </section>

  <section class="card landscape-back" aria-label="Card back, landscape">
    <div class="service-col garden">
      <h2>Garden</h2>
      <ul>
        <li>Garden Styling</li>
        <li>Plant Selection</li>
        <li>Garden Maintenance</li>
        <li>Mowing</li>
        <li>Local Nurseries Marrow</li>
      </ul>
    </div>
    <div class="service-col home">
      <h2>Home</h2>
      <ul>
        <li>Interior Styling</li>
        <li>Furniture Selection</li>
        <li>Setting Up Home (after move)</li>
        <li>Hedging</li>
        <li>Merchandise and Stylist for Work</li>
      </ul>
    </div>
    <svg class="stripe" viewBox="0 0 471 16" preserveAspectRatio="none" aria-hidden="true">
      <rect width="471" height="16" fill="var(--melon)"/>
      <polygon points="0,0 281,0 251,16 0,16" fill="var(--forest)"/>
    </svg>
  </section>

  <p class="caption title">My suggestion</p>
  <p class="caption front">Front</p>
  <p class="caption back">Back</p>

  <section class="card portrait portrait-front" aria-label="Card front, portrait">
    <svg class="split" width="261" height="470" viewBox="0 0 261 470" aria-hidden="true">
      <polygon points="0,298 261,190 261,470 0,470" fill="var(--melon-bright)"/>
      <line x1="0" y1="298" x2="261" y2="190" stroke="#fff" stroke-width="1.2"/>
    </svg>
    <span class="wordmark">Brambleway</span>
    <p class="tagline">Home and Garden Styling</p>
    <p class="phone"><svg width="13" height="16" viewBox="0 0 13 16" aria-hidden="true"><path d="M3 1 L5 4.5 L3.6 6 Q5 9.5 7.5 11.5 L9 10 L12 12.5 L10.5 15 Q3 13 1 4 Z" fill="none" stroke="#fff" stroke-width="1.4" stroke-linejoin="round"/></svg>0437619204</p>
    <p class="email">brambleaystudio@kelnor.net.au</p>
  </section>

  <section class="card portrait portrait-back" aria-label="Card back, portrait">
    <svg class="split" width="261" height="470" viewBox="0 0 261 470" aria-hidden="true">
      <polygon points="0,191 261,297 261,470 0,470" fill="var(--melon-bright)"/>
      <line x1="0" y1="191" x2="261" y2="297" stroke="#fff" stroke-width="1.2"/>
    </svg>
    <div class="service-col garden">
      <h2>Garden</h2>
      <ul>
        <li>Garden Styling</li>
        <li>Plant Selection</li>
        <li>Arrangement Garden Maintenance</li>
        <li>Mowing</li>
        <li>Local Nurseries Marrow and Finch</li>
      </ul>
    </div>
    <div class="service-col home">
      <h2>Home</h2>
      <ul>
        <li>Interior Styling</li>
        <li>Furniture Selection</li>
        <li>Setting Up Home (after move)</li>
        <li>Hedging</li>
        <li>Merchandise and Stylist for Work</li>
      </ul>
    </div>
  </section>

</main>
</body>
</html>
```